Tech business card design

We need an amazing business card design for our new business 'Pexla' a marketing tech startup based in Sydney, Australia. We provide an online marketplace for businesses to search and buy advertising media, connect with service providers and learn more about marketing. We wish to communicate 'cool tech', reliability and professionalism and design based around our logo.

Target Market(s)

Business Owners

Contact Information for Business Card

Name
Position
Email Address
Website
Phone Number

Font styles to use
Other font styles liked:
• Avenir & Avenir Next

Colors

Designer to choose colors to be used in the design.

```html
<!DOCTYPE html>
<html lang="en">
<head>
<meta charset="utf-8">
<title>Pexla business card</title>
<link rel="stylesheet" href="https://fonts.googleapis.com/css2?family=Work+Sans:wght@400;600;800&display=swap">
<style>
  :root {
    --navy: #12133d;
    --white: #ffffff;
    --backdrop: #a9a9a9;
    --muted: #6d6e7a;
    --rule: #2a2b55;
  }
  * { box-sizing: border-box; margin: 0; padding: 0; }
  html, body { width: 1200px; height: 930px; overflow: hidden; }
  body {
    background: var(--backdrop);
    font-family: "Work Sans", sans-serif;
    position: relative;
  }
  .card {
    position: absolute;
    left: 250px;
    width: 700px;
    height: 400px;
    border-radius: 26px;
    box-shadow: 0 6px 18px rgba(0,0,0,0.25);
  }
  .card--front {
    top: 40px;
    background: var(--navy);
    display: flex;
    align-items: center;
    justify-content: center;
  }
  .card--back {
    top: 490px;
    background: var(--white);
    color: var(--navy);
  }
  .wordmark {
    font-weight: 800;
    letter-spacing: -1px;
    line-height: 1;
  }
  .card--front .wordmark { color: var(--white); font-size: 110px; }
  .card--back .wordmark {
    position: absolute;
    top: 40px;
    right: 70px;
    font-size: 70px;
    color: var(--navy);
  }
  .rule {
    position: absolute;
    left: 70px;
    right: 40px;
    top: 252px;
    height: 2px;
    background: var(--rule);
  }
  .person { position: absolute; left: 70px; top: 192px; }
  .person__name { font-size: 26px; font-weight: 600; color: var(--navy); }
  .person__role { font-size: 16px; color: var(--muted); margin-top: 2px; }
  .address {
    position: absolute;
    right: 40px;
    top: 200px;
    text-align: right;
    font-size: 17px;
    color: var(--muted);
    line-height: 1.35;
  }
  .contacts {
    position: absolute;
    left: 70px;
    top: 272px;
    list-style: none;
    font-size: 17px;
    color: var(--muted);
  }
  .contacts li { display: flex; align-items: center; gap: 12px; height: 28px; }
  .contacts svg { width: 13px; height: 13px; fill: none; stroke: var(--navy); stroke-width: 2; }
</style>
</head>
<body>
  <section class="card card--front">
    <span class="wordmark">pexla</span>
  </section>

  <section class="card card--back">
    <span class="wordmark">pexla</span>
    <div class="person">
      <p class="person__name">Daniel Hart</p>
      <p class="person__role">Director</p>
    </div>
    <p class="address">18 Wattle Lane<br>Sydney, NSW 2000</p>
    <div class="rule"></div>
    <ul class="contacts">
      <li>
        <svg viewBox="0 0 16 16"><path d="M3 2l3 0 1 4-2 1a8 8 0 0 0 4 4l1-2 4 1v3a1 1 0 0 1-1 1A12 12 0 0 1 2 3a1 1 0 0 1 1-1z"/></svg>
        +61 2 5550 1842
      </li>
      <li>
        <svg viewBox="0 0 16 16"><rect x="1.5" y="3.5" width="13" height="9"/><path d="M1.5 3.5l6.5 5 6.5-5"/></svg>
        info@pexla.com
      </li>
      <li>
        <svg viewBox="0 0 16 16"><circle cx="8" cy="8" r="6.5"/><path d="M1.5 8h13M8 1.5c-3 3.5-3 9.5 0 13M8 1.5c3 3.5 3 9.5 0 13"/></svg>
        www.pexla.com
      </li>
    </ul>
  </section>
</body>
</html>
```